Marrowby Water Taxi and Transport Business Card

I need business cards for my new water taxi and freight transport business I have started here in Kodiak Alaska. Kodiak is a remote island in the middle of the gulf of Alaska. There are seven native villages around the island and Kodiak is the #2 fishing port in the United States. We also have the largest Coast Guard Base in the U.S. My company will be providing water taxi and freight transport logistics to the villages and many hunting and fishing lodges as well as remote properties around the island.

I would like a business card that isn't status quo, something that stands out, either in feel or appearance. I do like clean minimal designs but it needs to have the necessary contact info on it.

Target Market(s)

remote lodge / property owners, residents of the many villages around Kodiak and any one wanting to enjoy the great outdoors of Kodiak Alaska

Industry/Entity Type

Business

Contact Information for Business Card

I like clean simple designs that aren't cluttered but still provide the necessary information

Colors
0255a3
3277b5
33a4d5
9bcb3c
add136
fbed22
ffc214
f78f20
f37122

Requirements
Must have
• logo and contact info
• Captain Mason Elwick
• www.marrowbyferryline.com
• mason@marrowbyferryline.com

```html
<!DOCTYPE html>
<html lang="en">
<head>
<meta charset="utf-8">
<title>Marrowby Water Taxi and Transport – Business Card</title>
<link href="https://fonts.googleapis.com/css2?family=Open+Sans:wght@400;700&display=swap" rel="stylesheet">
<style>
  :root {
    --navy: #0255a3;
    --deep: #0a3f8f;
    --mid: #3277b5;
    --sky: #33a4d5;
    --accent: #f7a21e;
    --white: #ffffff;
    --stage: #e9ecef;
  }
  * { margin: 0; padding: 0; box-sizing: border-box; }
  html, body { width: 1200px; height: 913px; overflow: hidden; }
  body {
    background: var(--stage);
    font-family: "Open Sans", Arial, sans-serif;
    position: relative;
  }
  .card {
    position: absolute;
    top: 308px;
    width: 520px;
    height: 297px;
    border-radius: 14px;
    overflow: hidden;
    box-shadow: 0 8px 24px rgba(0,0,0,.18);
  }
  .card--front { left: 50px; background: var(--white); }
  .card--back {
    left: 630px;
    background: linear-gradient(135deg, #3b8fd6 0%, var(--navy) 55%, var(--deep) 100%);
  }
  .card__art { position: absolute; inset: 0; }

  .brand-name {
    position: absolute;
    left: 110px;
    top: 38px;
    width: 240px;
    color: var(--mid);
    font-weight: 700;
    font-size: 20px;
    line-height: 1.3;
    text-align: center;
  }

  .holder {
    position: absolute;
    right: 22px;
    top: 134px;
    color: var(--navy);
    font-weight: 700;
    font-size: 17px;
    white-space: nowrap;
  }
  .contact {
    position: absolute;
    left: 24px;
    bottom: 22px;
    list-style: none;
    color: var(--white);
    font-size: 13px;
    line-height: 1.6;
  }
  .contact li { display: flex; align-items: center; gap: 8px; white-space: nowrap; }
  .contact svg { width: 12px; height: 12px; flex: none; }

  .back-name {
    position: absolute;
    left: 70px; right: 40px; top: 108px;
    text-align: center;
    color: var(--white);
    font-weight: 700;
    font-size: 26px;
    line-height: 1.3;
  }
</style>
</head>
<body>

<section class="card card--front" aria-label="Card front">
  <svg class="card__art" viewBox="0 0 520 297" preserveAspectRatio="none" aria-hidden="true">
    <defs>
      <linearGradient id="frontBlue" x1="0" y1="0" x2="1" y2="1">
        <stop offset="0" stop-color="#1a6cc0"/>
        <stop offset="1" stop-color="#0a3f8f"/>
      </linearGradient>
    </defs>
    <polygon points="0,212 196,212 226,165 520,165 520,297 0,297" fill="url(#frontBlue)"/>
    <polygon points="226,165 248,128 520,128 520,165" fill="#33a4d5"/>
    <polygon points="0,212 196,212 190,222 0,222" fill="#3277b5"/>
  </svg>

  <p class="brand-name">Marrowby Water Taxi and Transport</p>

  <p class="holder">Captain Mason Elwick</p>

  <ul class="contact">
    <li>
      <svg viewBox="0 0 12 12" aria-hidden="true"><rect x="0.5" y="2" width="11" height="8" fill="none" stroke="#f7a21e"/><polyline points="0.5,2 6,7 11.5,2" fill="none" stroke="#f7a21e"/></svg>
      mason@marrowbyferryline.com
    </li>
    <li>
      <svg viewBox="0 0 12 12" aria-hidden="true"><circle cx="6" cy="6" r="5.3" fill="none" stroke="#f7a21e"/><ellipse cx="6" cy="6" rx="2.3" ry="5.3" fill="none" stroke="#f7a21e"/><line x1="0.7" y1="6" x2="11.3" y2="6" stroke="#f7a21e"/></svg>
      www.marrowbyferryline.com
    </li>
  </ul>
</section>

<section class="card card--back" aria-label="Card back">
  <svg class="card__art" viewBox="0 0 520 297" preserveAspectRatio="none" aria-hidden="true">
    <rect x="0" y="0" width="30" height="70" fill="#33a4d5"/>
    <rect x="0" y="70" width="30" height="60" fill="#ffffff"/>
    <rect x="0" y="130" width="30" height="60" fill="#1f86d2"/>
    <rect x="0" y="190" width="30" height="60" fill="#ffffff"/>
    <rect x="0" y="250" width="30" height="47" fill="#33a4d5"/>
  </svg>
  <p class="back-name">Marrowby Water Taxi and Transport</p>
</section>

</body>
</html>
```